Business Cards for new orthopaedic surgery practice

My husband and I are starting our own orthopaedic surgery practice. We are looking for a business card that is uniform, but one will have my name/title and the other will have his. You can just create one design with my name on it for now. But when I choose your design as the winning design I will ask that you add another copy with his name/title.

We are looking for classy, simple, elite all in one. We like dark blues/a little gold/yellow. Something that goes with our logo. We want our logo incorporated. Here is all the info you need:
Business name: RV Bone & Vitality Center
Location: 38517 North Willowmere Ave
Brookhaven Bay, FL 34012
Phone: 954-218-4063
Fax: 954-582-7341
Email: info@myrvbonecare.example

Names: Lydia Vance, M.D.
Board Certified Hand and Upper Extremity Surgeon

Ebo Dansu, M.D.
Board Certified Hip & Knee Replacement/General Orthopaedic Surgeon

Can decide what you want to put on the back. Maybe a slogan:
Grounded in Care. Centered on You

I am just going to upload our logo. The only thing is if we select you as the winning design, the location, and phone numbers may change. We will need your help to update that once fully solidified.

Industry/Entity Type

Medical

Contact Information for Business Card

Colors
0054AA
0677BA
7BADD7
CADEEF
E8F1F8
0094D4
00A9DD
6FCCEA
C7EBF8
E9F6FB

Requirements
Must have
• class, appeal,
Should not have
• We want to air on the side of masculine if we are looking at masculine vs. feminine feel. But we still want it classy, sophisticated, and something we will love

```html
<!DOCTYPE html>
<html lang="en">
<head>
<meta charset="utf-8">
<title>RV Bone &amp; Vitality Center — Business Cards</title>
<link href="https://fonts.googleapis.com/css2?family=Poppins:wght@400;500;600;700&display=swap" rel="stylesheet">
<style>
  :root {
    --stage: #2f2f31;
    --card-light: #ade3f3;
    --card-bright: #6ccbeb;
    --navy: #233f8f;
    --navy-soft: rgba(35, 63, 143, 0.08);
    --white: #ffffff;
  }
  * { box-sizing: border-box; margin: 0; padding: 0; }
  html, body { width: 1200px; height: 800px; overflow: hidden; }
  body {
    background: var(--stage);
    font-family: "Poppins", sans-serif;
    color: var(--navy);
    position: relative;
  }
  .card {
    position: absolute;
    border-radius: 18px;
    background: var(--card-light);
    overflow: hidden;
  }

  /* Back card (portrait) */
  .card-back { left: 90px; top: 120px; width: 320px; height: 560px; }
  .card-back__content {
    position: absolute;
    left: 50%; top: 50%;
    width: 560px; height: 320px;
    margin-left: -280px; margin-top: -160px;
    transform: rotate(-90deg);
  }
  .card-back__decor {
    position: absolute; left: 150px; top: 110px; width: 260px; height: 50px;
    border-radius: 25px;
    background: linear-gradient(90deg, transparent, var(--navy-soft), transparent);
  }
  .brand-block {
    position: absolute; left: 0; right: 0; top: 70px;
    display: flex; flex-direction: column; align-items: center; gap: 10px;
  }
  .brand-name {
    font-weight: 500; font-size: 24px; letter-spacing: 1.5px;
    text-transform: uppercase; color: var(--navy); text-align: center;
    display: flex; align-items: center; gap: 12px;
  }
  .brand-mark { width: 16px; height: 16px; background: var(--navy); flex: none; }
  .brand-rule { width: 300px; height: 1.5px; background: var(--navy); }
  .slogan-pill {
    position: absolute; left: 40px; right: 40px; bottom: 26px; height: 48px;
    border-radius: 24px; background: var(--navy); color: var(--white);
    display: flex; align-items: center; justify-content: center;
    font-size: 18px; letter-spacing: 1px;
  }

  /* Front card (landscape) */
  .card-front { left: 470px; top: 217px; width: 640px; height: 366px; }
  .card-front__panel {
    position: absolute; left: 0; top: 0; bottom: 0; width: 350px;
    background: var(--card-bright);
  }
  .spine-decor {
    position: absolute; top: 40px; bottom: 20px; width: 44px; border-radius: 22px;
    background: linear-gradient(180deg, var(--navy-soft), rgba(35,63,143,0.02));
  }
  .spine-decor--panel { left: 260px; top: 110px; }
  .spine-decor--side { left: 540px; }
  .name-tab {
    position: absolute; left: 0; top: 28px; width: 10px; height: 40px; background: var(--navy);
  }
  .doctor-name {
    position: absolute; left: 26px; top: 24px;
    font-weight: 700; font-size: 25px; letter-spacing: 0.5px; text-transform: uppercase;
  }
  .doctor-title {
    position: absolute; left: 26px; top: 58px;
    font-weight: 600; font-size: 8.5px; text-transform: uppercase; letter-spacing: 0.2px;
  }
  .contact-list { position: absolute; left: 0; top: 118px; list-style: none; }
  .contact-item {
    display: flex; align-items: center; height: 26px; margin-bottom: 14px;
    font-size: 16px; letter-spacing: 0.5px;
  }
  .contact-item--address { align-items: flex-start; line-height: 24px; height: auto; }
  .contact-tab {
    width: 46px; height: 26px; margin-right: 14px; flex: none;
    background: var(--navy); border-radius: 0 13px 13px 0;
    display: flex; align-items: center; justify-content: flex-end; padding-right: 4px;
  }
  .contact-icon {
    width: 18px; height: 18px; border-radius: 50%; background: var(--card-bright);
    display: flex; align-items: center; justify-content: center;
  }
  .card-front__brand {
    position: absolute; left: 380px; right: 20px; top: 150px;
    display: flex; align-items: center; gap: 12px;
  }
  .card-front__brand .brand-name {
    font-size: 19px; letter-spacing: 0.5px; line-height: 1.25; text-align: left;
    border-left: 1.5px solid var(--navy); padding-left: 12px;
  }
</style>
</head>
<body>

  <section class="card card-back" aria-label="Business card back">
    <div class="card-back__content">
      <div class="card-back__decor" role="img" aria-label="Faint spine illustration"></div>
      <div class="brand-block">
        <div class="brand-name"><span class="brand-mark"></span>RV Bone &amp; Vitality Center</div>
        <div class="brand-rule"></div>
      </div>
      <div class="slogan-pill">Grounded in Care. Centered on You</div>
    </div>
  </section>

  <section class="card card-front" aria-label="Business card front">
    <div class="card-front__panel"></div>
    <div class="spine-decor spine-decor--panel" role="img" aria-label="Faint spine illustration"></div>
    <div class="spine-decor spine-decor--side" role="img" aria-label="Faint spine illustration"></div>

    <div class="name-tab"></div>
    <h1 class="doctor-name">Lydia Vance, M.D.</h1>
    <p class="doctor-title">Board Certified Hand and Upper Extremity Surgeon</p>

    <ul class="contact-list">
      <li class="contact-item">
        <span class="contact-tab"><span class="contact-icon">
          <svg width="10" height="10" viewBox="0 0 24 24"><path fill="#233f8f" d="M6.6 10.8a15 15 0 0 0 6.6 6.6l2.2-2.2a1 1 0 0 1 1-.25 11.4 11.4 0 0 0 3.6.6 1 1 0 0 1 1 1V20a1 1 0 0 1-1 1A17 17 0 0 1 3 4a1 1 0 0 1 1-1h3.5a1 1 0 0 1 1 1c0 1.25.2 2.45.6 3.6a1 1 0 0 1-.25 1z"/></svg>
        </span></span>954-218-4063
      </li>
      <li class="contact-item">
        <span class="contact-tab"><span class="contact-icon">
          <svg width="10" height="10" viewBox="0 0 24 24"><path fill="#233f8f" d="M6 2h12v6H6zM4 9h16a2 2 0 0 1 2 2v6h-4v5H6v-5H2v-6a2 2 0 0 1 2-2zm4 8v3h8v-3z"/></svg>
        </span></span>954-582-7341
      </li>
      <li class="contact-item">
        <span class="contact-tab"><span class="contact-icon">
          <svg width="10" height="10" viewBox="0 0 24 24"><path fill="none" stroke="#233f8f" stroke-width="2.5" d="M3 5h18v14H3zM3 5l9 8 9-8"/></svg>
        </span></span>info@myrvbonecare.example
      </li>
      <li class="contact-item contact-item--address">
        <span class="contact-tab"><span class="contact-icon">
          <svg width="10" height="10" viewBox="0 0 24 24"><path fill="#233f8f" d="M12 2a7 7 0 0 0-7 7c0 5 7 13 7 13s7-8 7-13a7 7 0 0 0-7-7zm0 9.5A2.5 2.5 0 1 1 12 6.5a2.5 2.5 0 0 1 0 5z"/></svg>
        </span></span>
        <span>38517 North Willowmere Ave<br>Brookhaven Bay, FL 34012</span>
      </li>
    </ul>

    <div class="card-front__brand">
      <span class="brand-mark"></span>
      <div class="brand-name">RV Bone &amp;<br>Vitality<br>Center</div>
    </div>
  </section>

</body>
</html>
```